BrindleStaffing Business Card Design

We are a staffing company finding positions for dedicated nurses and physicians.

Target Market(s)

Business Professionals

Industry/Entity Type

Staffing

Contact Information for Business Card

Gordon Pratley
Chairman
417 39th Avenue South
SAINT PETERSBURG FL 33712
813-555-4172 Mobile
813-555-8036 Fax
gpratley@brindlestaffing.com
www.brindlestaffing.com

Font styles to use
Sans Serif

Colors
fbee3e
f04a50
f37122

Requirements
Must have
• Logo Attached, see colors below. We'd like to see Yellow, Orange and Red.

```html
<!DOCTYPE html>
<html lang="en">
<head>
<meta charset="utf-8">
<title>BrindleStaffing Business Card</title>
<link href="https://fonts.googleapis.com/css2?family=Roboto:wght@400;500;700&display=swap" rel="stylesheet">
<style>
  :root {
    --backdrop: #e4e4e4;
    --card: #ffffff;
    --brand-orange: #f37122;
    --brand-red: #f04a50;
    --brand-yellow: #fbee3e;
    --text-grey: #555a60;
  }
  html, body {
    margin: 0;
    padding: 0;
    width: 1125px;
    height: 1200px;
    overflow: hidden;
    background: var(--backdrop);
    font-family: "Roboto", Arial, sans-serif;
  }
  .card {
    position: absolute;
    left: 166px;
    width: 800px;
    height: 457px;
    border-radius: 24px;
    overflow: hidden;
    background: var(--card);
  }
  .card--front { top: 103px; }
  .card--back { top: 619px; background: var(--brand-orange); }

  .brand-name {
    position: absolute;
    font-weight: 700;
    letter-spacing: -1px;
    white-space: nowrap;
    line-height: 1;
  }
  .card--front .brand-name {
    left: 57px;
    top: 184px;
    font-size: 49px;
    color: var(--brand-orange);
  }
  .divider-plus {
    position: absolute;
    left: 408px;
    top: 114px;
  }
  .divider {
    position: absolute;
    left: 415px;
    top: 135px;
    width: 3px;
    height: 157px;
    background: var(--brand-red);
  }
  .person-name {
    position: absolute;
    left: 454px;
    top: 106px;
    margin: 0;
    font-size: 34px;
    font-weight: 700;
    color: var(--brand-orange);
  }
  .person-title {
    position: absolute;
    left: 454px;
    top: 145px;
    margin: 0;
    font-size: 20px;
    font-weight: 500;
    color: var(--brand-red);
  }
  .contact-list {
    position: absolute;
    left: 454px;
    top: 193px;
    margin: 0;
    padding: 0;
    list-style: none;
  }
  .contact-list li {
    display: flex;
    align-items: center;
    height: 25.5px;
    font-size: 19px;
    color: var(--text-grey);
  }
  .contact-list svg {
    width: 18px;
    height: 18px;
    margin-right: 12px;
    flex: none;
  }
  .address-band {
    position: absolute;
    left: 0;
    top: 385px;
    width: 100%;
    height: 38px;
    background: var(--brand-orange);
    color: #fff;
    font-size: 20px;
    line-height: 38px;
    text-align: center;
  }

  .back-pattern {
    position: absolute;
    inset: 0;
    background: linear-gradient(180deg, #f5823a, var(--brand-orange));
  }
  .card--back .brand-name {
    left: 0;
    width: 100%;
    top: 176px;
    text-align: center;
    font-size: 66px;
    color: #fff;
  }
  .web-band {
    position: absolute;
    left: 0;
    top: 385px;
    width: 100%;
    height: 37px;
    background: #fff;
    color: var(--brand-orange);
    font-size: 18px;
    font-weight: 700;
    letter-spacing: 5px;
    line-height: 37px;
    text-align: center;
  }
</style>
</head>
<body>

<section class="card card--front">
  <div class="brand-name">BrindleStaffing</div>

  <svg class="divider-plus" width="17" height="17" viewBox="0 0 17 17" aria-hidden="true">
    <rect x="6" y="0" width="5" height="17" fill="#f37122"/>
    <rect x="0" y="6" width="17" height="5" fill="#f37122"/>
  </svg>
  <div class="divider"></div>

  <h1 class="person-name">Gordon Pratley</h1>
  <p class="person-title">Chairman</p>

  <ul class="contact-list">
    <li>
      <svg viewBox="0 0 18 18" aria-hidden="true"><rect x="4" y="0.5" width="10" height="17" rx="2" fill="#f37122"/><rect x="6" y="3" width="6" height="10" fill="#fff"/></svg>
      813-555-4172
    </li>
    <li>
      <svg viewBox="0 0 18 18" aria-hidden="true"><rect x="4" y="1" width="10" height="6" fill="#f37122"/><rect x="1" y="7" width="16" height="8" rx="2" fill="#f37122"/><rect x="5" y="11" width="8" height="6" fill="#fff" stroke="#f37122"/></svg>
      813-555-8036
    </li>
    <li>
      <svg viewBox="0 0 18 18" aria-hidden="true"><rect x="1" y="4" width="16" height="11" fill="#f37122"/><path d="M1 4 L9 10 L17 4" fill="none" stroke="#fff" stroke-width="1.5"/></svg>
      gpratley@brindlestaffing.com
    </li>
    <li>
      <svg viewBox="0 0 18 18" aria-hidden="true"><circle cx="9" cy="9" r="8" fill="#f37122"/><path d="M4 6 Q7 5 8 8 T6 13 M11 3 Q13 7 15 8 M10 11 Q13 11 13 15" fill="none" stroke="#fff" stroke-width="1.4"/></svg>
      www.brindlestaffing.com
    </li>
  </ul>

  <div class="address-band">417 39th Avenue South, SAINT PETERSBURG FL 33712</div>
</section>

<section class="card card--back">
  <div class="back-pattern" role="img" aria-label="Repeating pattern of soft orange plus shapes"></div>
  <div class="brand-name">BrindleStaffing</div>
  <div class="web-band">www.brindlestaffing.com</div>
</section>

</body>
</html>
```